I need a book cover designed for "Generous Momentum. Where Winning Falls Short." The book encourages businesses to take up a social mission (that is, to have a social impact, such as corporate social responsibility.) in doing so, they find a greater sense of purpose, their employees and the community are more engaged, and their business grows. I use stories from my podcast Civic Purpose Uprising. 2 key word/phrases that may help t think about are Philanthropy and Corporate Social Responsibility.
This book will be followed by 1 or 2 other books. Another seies of books will also soon requre work.

The market is Mid-sized business owners and CEOs. They have built up the business to a successful place but now find that doesn't bring fulfilment or happiness. The cover needs to have a business or corporate feel.
The Colouring of the book, focus on blues and purples.
This will be a thin book - a quick and easy read of around 110 pages. It is 5x8 inches.
I would be happy to have a photo of me incorporated, but not the focus. I could have a photo done as directed by the designer, as I am planning to have a photoshoot done soon.
Fonts - Please chose a font with the rounded "a", such as in the Century Gothic font, however, open to suggestions.
The back cover will include:
o A book blurb – still to be written
o 2 or 3 endorsements
o Publishing logo (as it is my own publishing company.
o ISBN and barcode
On the spine
• Generous Momentum
• Melissa Garrow
• Publisher logo icon

For your interest: Melissa is a Speaker, Author, podcaster and Trusted Advisor to Authentic Influencers. Through nourishing community, Melissa maximises the potential of business and influences change.

Target Market(s)

The market is Mid-sized business owners and CEOs. They have built up the business to a successful place but now find that doesn't bring fulfillment or happiness. The cover needs to have a business or corporate feel.

Industry/Entity Type

This is business/corporate book

Font styles to use
Other font styles liked:
• Please chose a font with the rounded "a", such as in the Century Gothic font, however, open to suggestions.

Colors
0054AA
0677BA
7BADD7
CADEEF
E8F1F8
A7469A
B969AE
D3A5CF
EDDBEB
F8F0F9
6B429C
8869AF
B7A5CE
E3DAEB
F3F0F8

Requirements
Must have
• An eye catching design with a business feel.
Nice to have
• I would be nice to edit me into the cover somehow - like Brambleton puts himself in the background of his movies. I can have photos taken to match .

```html
<!DOCTYPE html>
<html lang="en">
<head>
<meta charset="utf-8">
<title>Generous Momentum — Book Cover</title>
<link rel="stylesheet" href="https://fonts.googleapis.com/css2?family=Rye&family=Playfair+Display:wght@700;900&display=swap">
<style>
  :root {
    --backdrop: #9dd6c5;
    --cover-white: #ffffff;
    --cover-fade: #f2f2f2;
    --royal-blue: #1a4599;
    --sun-yellow: #f5d33f;
    --text-white: #ffffff;
  }
  * { margin: 0; padding: 0; box-sizing: border-box; }
  html, body {
    width: 1200px; height: 857px; overflow: hidden;
    background: var(--backdrop);
  }
  .canvas { position: relative; width: 1200px; height: 857px; }
  .book-cover {
    position: absolute; left: 412px; top: 118px;
    width: 421px; height: 617px;
    background: linear-gradient(180deg, var(--cover-white) 30%, var(--cover-fade) 100%);
  }
  .edge-band { position: absolute; left: 0; width: 100%; background: var(--royal-blue); }
  .edge-band--top { top: 0; height: 26px; }
  .edge-band--bottom { bottom: 0; height: 27px; }

  .title-main {
    position: absolute; left: 30px; top: 26px; width: 354px; height: 53px;
    background: var(--sun-yellow); color: var(--royal-blue);
    font-family: "Rye", serif; font-size: 42px; line-height: 53px;
    text-align: center; letter-spacing: 2px;
  }
  .title-second {
    position: absolute; left: 30px; top: 79px; width: 354px; height: 32px;
    background: var(--royal-blue); color: var(--sun-yellow);
    font-family: "Playfair Display", serif; font-weight: 900; font-size: 20px;
    line-height: 32px; text-align: center; letter-spacing: 15px; padding-left: 15px;
  }
  .emblem-area {
    position: absolute; left: 93px; top: 145px; width: 246px; height: 228px;
    border-radius: 50%;
    background: radial-gradient(circle at 50% 50%, var(--cover-white) 20%, var(--royal-blue) 55%, var(--sun-yellow) 75%, var(--cover-white) 78%);
    opacity: 0.9;
  }
  .subtitle-panel {
    position: absolute; left: 30px; top: 397px; width: 354px; height: 111px;
    background: var(--royal-blue); text-align: center;
  }
  .subtitle-lead {
    margin-top: 10px; color: var(--text-white);
    font-family: "Playfair Display", serif; font-weight: 900; font-size: 23px;
    letter-spacing: 2px; line-height: 28px;
  }
  .subtitle-joiner {
    display: flex; align-items: center; justify-content: center; gap: 10px;
    color: var(--text-white); font-family: "Playfair Display", serif;
    font-weight: 700; font-size: 12px; line-height: 14px; letter-spacing: 1px;
  }
  .subtitle-joiner .rule { width: 92px; height: 2px; background: var(--text-white); }
  .subtitle-close {
    color: var(--sun-yellow); font-family: "Rye", serif; font-size: 36px;
    line-height: 50px; letter-spacing: 2px;
  }
  .author-band {
    position: absolute; left: 30px; top: 545px; width: 354px; height: 45px;
    background: var(--sun-yellow); color: var(--royal-blue);
    font-family: "Playfair Display", serif; font-weight: 900; font-size: 24px;
    line-height: 45px; text-align: center; letter-spacing: 4px;
  }
</style>
</head>
<body>
<main class="canvas">
  <section class="book-cover" aria-label="Book cover: Generous Momentum by Melissa Garrow">
    <div class="edge-band edge-band--top"></div>

    <h1 class="title-main">GENEROUS</h1>
    <div class="title-second">MOMENTUM</div>

    <div class="emblem-area" role="img" aria-label="Emblem of three interlocking striped rings in blue and yellow"></div>

    <div class="subtitle-panel">
      <p class="subtitle-lead">WHERE WINNING</p>
      <p class="subtitle-joiner"><span class="rule"></span>FALLS<span class="rule"></span></p>
      <p class="subtitle-close">SHORT</p>
    </div>

    <p class="author-band">MELISSA GARROW</p>

    <div class="edge-band edge-band--bottom"></div>
  </section>
</main>
</body>
</html>
```